Online interactive tutorial for year 2 to year 12 students in Australia

Website design for a new online tutorial for year 2 to year 12 students in Australia.

- The tutorial will be conducted via live webcam and within a dedicated interactive space
- The tutorial will be provided by high scoring undergraduates studying in top Australian universities.
- The tutors will be going through interviews & assessments & only top students are allowed to apply.
- Parents will do search and select tutor and have short 15 mins video interaction with potential tutors before booking them for their children for tutoring.
- hourly cost of booking (no monthly subscription or no hour limits)
- Tutors will have their own profile

Please see the attached for detailed page functionality.

The look and feel of the design must consider the following:
- must be educational but not dull and should stand out
- must appeal to younger generation - tutees (8-18 years), tutors (19-25), parents (30-50).
- Ideas for Logos (brivora.com.au but not confirmed)

Target Market(s)

tutees (8-18 years), tutors (19-25 years), parents (30-50 years).

Industry/Entity Type

Education

Coding

Coded - Design and coding required

Number of Pages Required

5+ page

Font styles to use
Serif

Requirements
Must have
• The look and feel of the design must consider the following:
• - must be educational but not dull and should stand out
• - must appeal to younger generation - tutees (8-18 years), tutors (19-25), parents (30-50).
Should not have
• Dullness

```html
<!DOCTYPE html>
<html lang="en">
<head>
<meta charset="utf-8">
<title>Brivora – Online Tutoring</title>
<link href="https://fonts.googleapis.com/css2?family=Montserrat:wght@400;600;700;800&family=Open+Sans:wght@400;600;700&display=swap" rel="stylesheet">
<style>
:root{
  --navy:#1f3a5a;
  --navy-dark:#152a43;
  --navy-deep:#0f1f33;
  --blue:#29a8e0;
  --blue-dark:#1d8fc4;
  --ink:#2b2b2b;
  --muted:#8a8f96;
  --line:#e4e7ea;
  --pale:#f4f6f8;
  --white:#ffffff;
}
*{box-sizing:border-box;margin:0;padding:0}
html,body{width:1200px;height:2924px;overflow:hidden}
body{font-family:"Open Sans",Arial,sans-serif;color:var(--ink);background:var(--white);font-size:13px;line-height:1.7}
h1,h2,h3,h4,.brand,.btn,.nav a{font-family:"Montserrat",Arial,sans-serif}
.wrap{width:1010px;margin:0 auto;position:relative}
.btn{display:inline-block;background:var(--blue);color:var(--white);font-size:12px;font-weight:700;letter-spacing:.5px;text-transform:uppercase;padding:12px 26px;border-radius:2px}

/* top bar */
.topbar{height:32px;border-bottom:1px solid var(--line);font-size:11px;color:var(--muted)}
.topbar .wrap{display:flex;justify-content:flex-end;gap:26px;align-items:center;height:32px}
.topbar span{display:flex;align-items:center;gap:6px}

/* header */
.header{height:108px}
.header .wrap{display:flex;justify-content:space-between;align-items:center;height:108px}
.brand{font-size:40px;font-weight:800;color:var(--navy);letter-spacing:1px;display:flex;align-items:center;gap:10px}
.brand i{width:14px;height:14px;background:var(--blue);display:block}
.nav{display:flex;gap:0}
.nav a{font-size:11px;font-weight:600;color:#555;text-decoration:none;padding:0 18px;border-left:1px solid var(--line);text-transform:uppercase}
.nav a:first-child{border-left:0;color:var(--blue)}

/* hero */
.hero{height:440px;position:relative;background:linear-gradient(90deg,#e9eef2 0%,#dfe6ec 35%,#c9b8a4 60%,#a7b7c6 100%)}
.hero .photo{position:absolute;inset:0}
.hero .wrap{height:440px}
.hero-text{position:absolute;left:80px;top:182px}
.hero-text h1{font-size:30px;font-weight:700;color:var(--navy);line-height:1.25}
.hero-text h1 small{display:block;font-size:24px;font-weight:600;margin-bottom:2px}
.hero-text .btn{margin-top:26px}
.arrow{position:absolute;top:198px;font-size:40px;color:#9aa3ab;font-family:Arial,sans-serif}

/* welcome */
.welcome{height:308px;text-align:center;padding-top:62px}
.section-title{font-size:25px;font-weight:700;color:var(--navy);text-transform:uppercase}
.welcome .sub{color:var(--blue);font-size:13px;font-weight:600;text-transform:uppercase;margin:6px 0 16px}
.welcome p{width:840px;margin:0 auto;font-size:11.5px;color:var(--muted)}

/* tutors */
.tutors{height:452px;background:var(--navy)}
.tutors .wrap{display:flex;height:452px;align-items:center;gap:32px}
.tutors-intro{width:222px;color:#cdd7e2}
.tutors-intro h2{font-size:26px;color:var(--white);font-weight:700;margin-bottom:14px}
.tutors-intro p{font-size:11px;line-height:1.8}
.dots{display:flex;gap:8px;margin-top:18px}
.dots b{width:18px;height:18px;border-radius:50%;background:var(--white);color:var(--navy);font-size:11px;display:flex;align-items:center;justify-content:center}
.card{width:236px;height:288px;background:var(--white);padding:12px;border-radius:2px}
.card .photo{height:112px;background:linear-gradient(135deg,#9aa7b4,#dfe3e8 60%,#b8c1cb)}
.card h3{font-size:13px;font-weight:600;color:var(--ink);margin:12px 0 6px}
.card p{font-size:10.5px;color:var(--muted);border-top:1px solid var(--line);padding-top:10px;line-height:1.6}
.card .btn{font-size:10px;padding:9px 22px;margin-top:16px}

/* how it works */
.how{height:464px;padding-top:58px}
.how .section-title{text-align:center}
.how .intro{width:860px;margin:14px auto 46px;text-align:center;font-size:11.5px;color:var(--muted)}
.how-row{display:flex;justify-content:space-between}
.how-row p{width:580px;font-size:11px;color:var(--muted);line-height:1.9}
.video{width:380px;height:210px;background:linear-gradient(135deg,#b88f6a,#d9c1a1 45%,#8e7a93);position:relative;border-radius:2px}
.video .play{position:absolute;left:50%;top:50%;width:46px;height:46px;margin:-23px 0 0 -23px}

/* registration */
.register{height:350px;background:linear-gradient(180deg,#22405f,#1a3350);text-align:center;color:#cdd7e2;padding-top:92px}
.register .section-title{color:var(--white)}
.register p{width:860px;margin:16px auto 28px;font-size:11.5px}

/* feedback */
.feedback{height:334px;padding-top:54px}
.feedback .section-title{text-align:center;margin-bottom:40px}
.quotes{display:flex;gap:60px}
.quote{width:475px;display:flex;gap:22px;align-items:flex-start}
.quote .avatar{width:90px;height:90px;border-radius:50%;flex:none;background:linear-gradient(135deg,#7f8d9c,#cfd6de)}
.quote p{font-size:11px;color:var(--muted);line-height:1.8}
.quote .who{margin-top:14px;font-size:12px;color:var(--muted)}
.quote .who strong{color:var(--blue)}

/* footer */
.footer{height:252px;background:var(--navy-dark);color:#b7c3d0;padding-top:32px}
.footer .wrap{display:flex;gap:56px}
.footer h4{font-size:13px;color:var(--white);font-weight:700;margin-bottom:18px;text-transform:uppercase}
.form{width:490px;display:grid;grid-template-columns:180px 1fr;gap:10px 14px}
.field{height:30px;background:var(--white);border-radius:2px;font-size:10px;color:var(--muted);padding:7px 10px}
.field.msg{grid-row:1 / span 2;height:70px}
.form .btn{justify-self:end;width:100px;text-align:center;padding:8px 0}
.contact{width:240px;font-size:11px}
.contact li{list-style:none;display:flex;gap:10px;margin-bottom:16px;align-items:flex-start}
.links{font-size:11px}
.links li{list-style:none;margin-bottom:6px}
.bottom{height:64px;background:var(--navy-deep);color:#8797a8;font-size:11px}
.bottom .wrap{display:flex;justify-content:space-between;align-items:center;height:64px}
.social{display:flex;gap:8px}
.social i{width:22px;height:22px;border-radius:50%;background:var(--blue);display:block}
</style>
</head>
<body>

<div class="topbar"><div class="wrap">
  <span><svg width="12" height="9" viewBox="0 0 12 9"><rect x=".5" y=".5" width="11" height="8" fill="none" stroke="#8a8f96"/><path d="M.5 .5L6 5l5.5-4.5" fill="none" stroke="#8a8f96"/></svg>info@brivora.com.au</span>
  <span><svg width="10" height="10" viewBox="0 0 10 10"><path d="M2 0l2 2.5-1.2 1.2a6 6 0 0 0 3.5 3.5L7.5 6 10 8 8.5 10C4 10 0 6 0 1.5z" fill="#8a8f96"/></svg>+61 2 5550 7812</span>
</div></div>

<header class="header"><div class="wrap">
  <div class="brand"><i></i>BRIVORA</div>
  <nav class="nav">
    <a href="#">Home</a><a href="#">About us</a><a href="#">Our services</a><a href="#">Schedules</a><a href="#">Feedback</a><a href="#">Contact us</a><a href="#">Register now</a>
  </nav>
</div></header>

<section class="hero">
  <div class="photo" role="img" aria-label="Photo of a smiling tutor and a young boy learning together at a laptop"></div>
  <span class="arrow" style="left:12px">‹</span><span class="arrow" style="right:12px">›</span>
  <div class="wrap">
    <div class="hero-text">
      <h1><small>ONLINE TRAINING FOR KIDS</small>FROM 2 YEARS TO 12 YEARS</h1>
      <a class="btn" href="#">Register now</a>
    </div>
  </div>
</section>

<section class="welcome">
  <h2 class="section-title">Welcome to Brivora</h2>
  <div class="sub">Online training for kids from 2 years to 12 years</div>
  <p>Our tutors are top students from leading Australian universities who have passed our interviews and assessments. Every lesson takes place live over webcam in a dedicated interactive space, so your child can ask questions, share work and learn at their own pace. Parents can search and select a tutor, meet them in a short fifteen minute video chat and book by the hour with no monthly subscription and no hour limits.</p>
</section>

<section class="tutors"><div class="wrap">
  <div class="tutors-intro">
    <h2>TUTORS</h2>
    <p>Each tutor is a high scoring undergraduate with a full profile showing subjects, year levels, results and availability. Browse profiles, compare experience and choose the tutor that suits your child best before booking a session.</p>
    <div class="dots"><b>‹</b><b>›</b></div>
  </div>
  <div class="card">
    <div class="photo" role="img" aria-label="Portrait photo of tutor Liam Hartley"></div>
    <h3>Liam Hartley</h3>
    <p>Maths and physics tutor for years 7 to 12, studying engineering.</p>
    <a class="btn" href="#">More details</a>
  </div>
  <div class="card">
    <div class="photo" role="img" aria-label="Portrait photo of tutor Marcus Venn"></div>
    <h3>Marcus Venn</h3>
    <p>English and history tutor for years 5 to 12, studying arts and law.</p>
    <a class="btn" href="#">More details</a>
  </div>
  <div class="card">
    <div class="photo" role="img" aria-label="Portrait photo of tutor Owen Castell"></div>
    <h3>Owen Castell</h3>
    <p>Science and reading tutor for years 2 to 8, studying education.</p>
    <a class="btn" href="#">More details</a>
  </div>
</div></section>

<section class="how"><div class="wrap">
  <h2 class="section-title">How it works</h2>
  <p class="intro">Finding the right tutor takes only a few steps. Search by subject and year level, view tutor profiles, book a free fifteen minute video chat to meet them and then book lessons by the hour whenever it suits your family.</p>
  <div class="how-row">
    <p>Start by creating a parent account and telling us about your child, their year level and the subjects they need help with. Our search shows tutors who match, with ratings, results and available times. Once you have found a few tutors you like, request a short video chat to meet them and make sure they are a good fit. When you are ready, book a lesson and pay only for the hours you use. Lessons run live over webcam inside our interactive classroom, with a shared whiteboard, document sharing and chat. After each lesson you can leave feedback, rebook the same tutor or try someone new. Tutors keep notes on progress so every session builds on the last one, and parents can follow along from their own dashboard at any time.</p>
    <div class="video" role="img" aria-label="Video still of a tutor helping a young girl with schoolwork">
      <svg class="play" viewBox="0 0 46 46"><circle cx="23" cy="23" r="22" fill="rgba(255,255,255,.85)"/><path d="M18 14l14 9-14 9z" fill="#29a8e0"/></svg>
    </div>
  </div>
</div></section>

<section class="register" role="img" aria-label="Dark blue banner with a faint photo of students studying">
  <h2 class="section-title">Tutor registration</h2>
  <p>Are you a high achieving undergraduate at a top Australian university? Apply to tutor with us, complete our interview and assessment, build your own profile and set the hours that fit around your study. Tutors teach from home using our live interactive classroom and get paid for every hour booked.</p>
  <a class="btn" href="#">⊕ Click here</a>
</section>

<section class="feedback"><div class="wrap">
  <h2 class="section-title">Tutor feedback</h2>
  <div class="quotes">
    <div class="quote">
      <div class="avatar" role="img" aria-label="Round portrait photo of a parent"></div>
      <div><p>Booking was simple and the video chat helped us pick the right tutor. My son now looks forward to maths and his marks have improved every term since starting.</p>
      <div class="who"><strong>Ruth Calder</strong> – parent, year 6</div></div>
    </div>
    <div class="quote">
      <div class="avatar" role="img" aria-label="Round portrait photo of a parent"></div>
      <div><p>Our tutor is patient and clear and fits lessons around our busy week. Paying by the hour with no subscription made it an easy decision for our whole family.</p>
      <div class="who"><strong>Dean Morrow</strong> – parent, year 9</div></div>
    </div>
  </div>
</div></section>

<footer class="footer"><div class="wrap">
  <div>
    <h4>Contact us</h4>
    <div class="form">
      <div class="field">Name</div><div class="field msg">Message</div>
      <div class="field">Email Address</div>
      <div class="field">Phone</div><a class="btn" href="#">Submit</a>
    </div>
  </div>
  <div class="contact">
    <h4>Get in touch</h4>
    <ul>
      <li><svg width="10" height="14" viewBox="0 0 10 14"><path d="M5 0a5 5 0 0 1 5 5c0 4-5 9-5 9S0 9 0 5a5 5 0 0 1 5-5z" fill="#29a8e0"/><circle cx="5" cy="5" r="2" fill="#152a43"/></svg>14 Harbour Lane, Sydney NSW 2000</li>
      <li><svg width="12" height="9" viewBox="0 0 12 9"><rect width="12" height="9" fill="#29a8e0"/><path d="M0 0l6 5 6-5" fill="none" stroke="#152a43"/></svg>info@brivora.com.au</li>
      <li><svg width="10" height="10" viewBox="0 0 10 10"><path d="M2 0l2 2.5-1.2 1.2a6 6 0 0 0 3.5 3.5L7.5 6 10 8 8.5 10C4 10 0 6 0 1.5z" fill="#29a8e0"/></svg>+61 2 5550 7812</li>
    </ul>
  </div>
  <div class="links">
    <h4>Quick links</h4>
    <ul><li>Tutor Registration</li><li>Parent Registration</li><li>About Us</li><li>Contact Us</li><li>Sitemap</li></ul>
  </div>
</div></footer>

<div class="bottom"><div class="wrap">
  <span>Copyright © 2016 brivora.com.au. All Rights Reserved.</span>
  <div class="social"><i></i><i></i><i></i><i></i></div>
</div></div>

</body>
</html>
```